Business Card Design

WE are looking for a premium quality Business Cards for a Law Firm . Copies of our current business card is attached.

Contact Information for Business Card

xyz

```html
<!DOCTYPE html>
<html lang="en">
<head>
<meta charset="utf-8">
<title>Ashcombe Lawyers – Business Cards</title>
<link rel="stylesheet" href="https://fonts.googleapis.com/css2?family=Libre+Baskerville:wght@400;700&display=swap">
<style>
  :root {
    --green: #10291d;
    --gold: #c9a862;
    --white: #ffffff;
    --ink: #111111;
    --backdrop: #232326;
    --serif: "Libre Baskerville", "Times New Roman", serif;
  }
  * { box-sizing: border-box; margin: 0; padding: 0; }
  html, body { width: 1200px; height: 780px; overflow: hidden; }
  body {
    background: var(--backdrop);
    font-family: var(--serif);
    position: relative;
  }
  .card {
    position: absolute;
    top: 230px;
    width: 560px;
    height: 320px;
    border-radius: 22px;
    overflow: hidden;
    box-shadow: 0 18px 40px rgba(0,0,0,.45);
  }
  /* ---------- back of card ---------- */
  .card--back { left: 27px; background: var(--green); color: var(--white); }
  .brand {
    position: absolute;
    display: flex;
    align-items: center;
    gap: 12px;
  }
  .brand__ring {
    border: 3px solid var(--gold);
    border-radius: 50%;
    flex: none;
  }
  .brand__words { display: flex; flex-direction: column; align-items: center; }
  .brand__name { font-weight: 700; letter-spacing: 1px; line-height: 1; }
  .brand__sub { color: var(--gold); letter-spacing: 6px; line-height: 1; margin-top: 4px; }
  .card--back .brand { left: 0; right: 0; top: 40px; justify-content: center; }
  .card--back .brand__ring { width: 58px; height: 58px; }
  .card--back .brand__name { font-size: 34px; color: var(--white); }
  .card--back .brand__sub { font-size: 11px; }

  .tagline {
    position: absolute;
    left: 0; right: 0; top: 142px;
    height: 24px;
    background: var(--gold);
    color: var(--green);
    font-weight: 700;
    font-size: 12px;
    letter-spacing: 1.5px;
    text-transform: uppercase;
    display: flex; align-items: center; justify-content: center;
  }
  .offices {
    position: absolute;
    left: 18px; right: 18px; top: 190px; bottom: 26px;
    display: flex;
  }
  .office {
    flex: 1;
    text-align: center;
    font-size: 10.5px;
    font-weight: 700;
    line-height: 1.55;
    padding: 0 8px;
  }
  .office + .office { border-left: 1px solid rgba(255,255,255,.8); }
  .office__city {
    color: var(--gold);
    font-size: 14px;
    letter-spacing: .5px;
    margin-bottom: 4px;
  }
  .office__phone { display: inline-flex; align-items: center; gap: 5px; }
  .icon { width: 11px; height: 11px; flex: none; }

  /* ---------- front of card ---------- */
  .card--front { right: 27px; background: var(--white); color: var(--ink); }
  .front-art { position: absolute; inset: 0; }
  .holder {
    position: absolute;
    right: 86px; top: 22px;
    text-align: right;
  }
  .holder__name {
    color: var(--gold);
    font-size: 30px;
    font-weight: 700;
    letter-spacing: 1px;
    line-height: 1.1;
  }
  .holder__role, .holder__quals { font-size: 12.5px; font-weight: 700; line-height: 1.5; }
  .card--front .brand { left: 28px; top: 112px; gap: 9px; }
  .card--front .brand__ring { width: 34px; height: 34px; }
  .card--front .brand__name { font-size: 20px; color: var(--green); }
  .card--front .brand__sub { font-size: 8px; letter-spacing: 4.5px; }
  .contact {
    position: absolute;
    left: 28px; top: 170px;
    font-size: 13px;
    font-weight: 700;
    line-height: 1.45;
  }
  .contact__address { margin-bottom: 8px; }
  .contact__list { list-style: none; }
  .contact__list li { display: flex; align-items: center; gap: 8px; }
  .contact__list .icon { width: 13px; height: 13px; }
</style>
</head>
<body>

<section class="card card--back" aria-label="Business card back">
  <div class="brand">
    <span class="brand__ring" aria-hidden="true"></span>
    <div class="brand__words">
      <span class="brand__name">ASHCOMBE</span>
      <span class="brand__sub">LAWYERS</span>
    </div>
  </div>

  <div class="tagline">Clear Advice. Strong Results. Every Time</div>

  <div class="offices">
    <div class="office">
      <div class="office__city">MELBOURNE</div>
      Level 12, 88 Harbour Street,<br>MELBOURNE, VIC 3000<br>
      <span class="office__phone">
        <svg class="icon" viewBox="0 0 24 24" aria-hidden="true"><path fill="#c9a862" d="M6.6 10.8a15 15 0 0 0 6.6 6.6l2.2-2.2c.3-.3.7-.4 1-.2 1.1.4 2.3.6 3.6.6.6 0 1 .4 1 1V20c0 .6-.4 1-1 1A17 17 0 0 1 3 4c0-.6.4-1 1-1h3.5c.6 0 1 .4 1 1 0 1.3.2 2.5.6 3.6.1.3 0 .7-.2 1z"/></svg>
        +61 03 5550 1824
      </span>
    </div>
    <div class="office">
      <div class="office__city">SYDNEY</div>
      Level 9, Regent House<br>42 Market Lane<br>PARRAMATTA, NSW 2150<br>
      <span class="office__phone">
        <svg class="icon" viewBox="0 0 24 24" aria-hidden="true"><path fill="#c9a862" d="M6.6 10.8a15 15 0 0 0 6.6 6.6l2.2-2.2c.3-.3.7-.4 1-.2 1.1.4 2.3.6 3.6.6.6 0 1 .4 1 1V20c0 .6-.4 1-1 1A17 17 0 0 1 3 4c0-.6.4-1 1-1h3.5c.6 0 1 .4 1 1 0 1.3.2 2.5.6 3.6.1.3 0 .7-.2 1z"/></svg>
        +61 02 5550 3391
      </span>
    </div>
    <div class="office">
      <div class="office__city">PERTH</div>
      Level 21, Kestrel Tower<br>75 Riverside Terrace<br>PERTH, WA 6000<br>
      <span class="office__phone">
        <svg class="icon" viewBox="0 0 24 24" aria-hidden="true"><path fill="#c9a862" d="M6.6 10.8a15 15 0 0 0 6.6 6.6l2.2-2.2c.3-.3.7-.4 1-.2 1.1.4 2.3.6 3.6.6.6 0 1 .4 1 1V20c0 .6-.4 1-1 1A17 17 0 0 1 3 4c0-.6.4-1 1-1h3.5c.6 0 1 .4 1 1 0 1.3.2 2.5.6 3.6.1.3 0 .7-.2 1z"/></svg>
        +61 08 5550 7265
      </span>
    </div>
  </div>
</section>

<section class="card card--front" aria-label="Business card front">
  <svg class="front-art" viewBox="0 0 560 320" aria-hidden="true">
    <rect x="496" y="0" width="64" height="16" fill="#c9a862"/>
    <path d="M560 150 C520 150 500 175 492 215 C470 290 330 316 120 320 L560 320 Z" fill="#10291d"/>
    <path d="M478 262 C430 300 320 316 120 320" fill="none" stroke="#c9a862" stroke-width="5"/>
    <circle cx="452" cy="178" r="66" fill="#ffffff" stroke="#c9a862" stroke-width="6"/>
  </svg>

  <div class="holder">
    <div class="holder__name">DANIEL MERCER</div>
    <div class="holder__role">Director and Principal Solicitor</div>
    <div class="holder__quals">MBA, Juris Doctor</div>
  </div>

  <div class="brand">
    <span class="brand__ring" aria-hidden="true"></span>
    <div class="brand__words">
      <span class="brand__name">ASHCOMBE</span>
      <span class="brand__sub">LAWYERS</span>
    </div>
  </div>

  <div class="contact">
    <p class="contact__address">Suite 310, Linden Chambers,<br>215 Little Bourke Street,<br>Melbourne VIC 3000</p>
    <ul class="contact__list">
      <li>
        <svg class="icon" viewBox="0 0 24 24" aria-hidden="true"><path fill="#c9a862" d="M6.6 10.8a15 15 0 0 0 6.6 6.6l2.2-2.2c.3-.3.7-.4 1-.2 1.1.4 2.3.6 3.6.6.6 0 1 .4 1 1V20c0 .6-.4 1-1 1A17 17 0 0 1 3 4c0-.6.4-1 1-1h3.5c.6 0 1 .4 1 1 0 1.3.2 2.5.6 3.6.1.3 0 .7-.2 1z"/></svg>
        +61 7 5550 2148
      </li>
      <li>
        <svg class="icon" viewBox="0 0 24 24" aria-hidden="true"><rect x="6" y="2" width="12" height="20" rx="2" fill="none" stroke="#c9a862" stroke-width="2.4"/></svg>
        +61 0400 555 917
      </li>
      <li>
        <svg class="icon" viewBox="0 0 24 24" aria-hidden="true"><circle cx="12" cy="12" r="10" fill="#c9a862"/><path d="M2 12h20M12 2c3 3 3 17 0 20M12 2c-3 3-3 17 0 20" fill="none" stroke="#fff" stroke-width="1.4"/></svg>
        www.ashcombelawyers.com.au
      </li>
      <li>
        <svg class="icon" viewBox="0 0 24 24" aria-hidden="true"><rect x="2" y="5" width="20" height="14" rx="1.5" fill="#c9a862"/><path d="M2.5 6l9.5 7 9.5-7" fill="none" stroke="#fff" stroke-width="1.6"/></svg>
        daniel@ashcombelawyers.com.au
      </li>
    </ul>
  </div>
</section>

</body>
</html>
```